Website for Torvel Capital - investment banking firm

We have a corporate identity (thanks to Ravinka/31842) and want to extend that into a website design.  See the attached zipped files.
We have software folks in-house to do the coding.
See the attached Project Brief & Notes for more details.  Don't worry about the actual text - lorem ipsum will be fine.
The server will be Apache.
Thank you!
Desmond

Industry/Entity Type
Investment

```html
<!DOCTYPE html>
<html lang="en">
<head>
<meta charset="utf-8">
<title>Torvel Capital – Investment Banking</title>
<link href="https://fonts.googleapis.com/css2?family=Noto+Serif:ital,wght@0,400;0,700;1,400&family=Open+Sans:ital,wght@0,400;0,600;1,400&display=swap" rel="stylesheet">
<style>
  :root {
    --brand-blue: #2b5aa6;
    --brand-blue-dark: #1f4a93;
    --heading-blue: #24539b;
    --text: #555;
    --text-dark: #333;
    --card-bg: #f2f2f2;
    --rule: #e4e4e4;
    --footer-top: #8a8a8a;
    --footer-bottom: #5f5f5f;
    --serif: 'Noto Serif', Georgia, serif;
    --sans: 'Open Sans', Arial, sans-serif;
  }
  * { box-sizing: border-box; margin: 0; padding: 0; }
  html, body { width: 928px; height: 1200px; overflow: hidden; background: #fff; }
  body { position: relative; font-family: var(--sans); color: var(--text); }
  .abs { position: absolute; }

  .topbar { left: 0; top: 0; width: 928px; height: 32px; border-bottom: 1px solid var(--rule); }
  .lang { right: 104px; top: 10px; font-size: 10px; color: #666; }

  .header { left: 0; top: 32px; width: 928px; height: 60px; border-bottom: 1px solid #ddd; background: #fff; }
  .brand { left: 101px; top: 14px; display: flex; align-items: center; gap: 8px; }
  .brand-mark { width: 26px; height: 26px; background: var(--brand-blue); }
  .brand-name { font-family: var(--serif); font-size: 18px; color: var(--brand-blue); letter-spacing: .5px; }
  .nav { left: 0; top: 0; width: 928px; height: 60px; font-family: var(--serif); font-size: 10.5px; color: #555; }
  .nav a { position: absolute; top: 25px; color: inherit; text-decoration: none; }
  .nav a.active { color: var(--brand-blue); }
  .nav-active-bar { left: 405px; top: 0; width: 38px; height: 3px; background: var(--brand-blue); }

  .hero { left: 0; top: 92px; width: 928px; height: 316px;
    background: linear-gradient(100deg, #d9d6d2 0%, #c9c2bb 30%, #b9a99c 48%, #e6dcd4 62%, #d8b8a4 78%, #e0e4e8 100%); }
  .hero-caption { left: 102px; background: rgba(36,78,150,.88); color: #fff; font-family: var(--serif); font-size: 24px; padding: 0 14px; height: 44px; line-height: 44px; white-space: nowrap; }
  .hero-arrow { top: 232px; width: 36px; height: 37px; background: rgba(90,90,90,.75); }

  .service-card { top: 451px; width: 170px; height: 184px; background: var(--card-bg); text-align: center; padding-top: 16px; }
  .service-card.featured { background: linear-gradient(180deg, #3a70c6, var(--brand-blue-dark)); color: #fff; }
  .service-icon { width: 54px; height: 54px; border-radius: 50%; background: #fff; margin: 0 auto; display: flex; align-items: center; justify-content: center; box-shadow: 0 0 0 1px #ddd; }
  .service-title { font-family: var(--serif); font-size: 14px; color: #333; margin-top: 12px; line-height: 19px; }
  .featured .service-title { color: #fff; }
  .service-text { font-size: 9px; line-height: 14px; margin: 8px 10px 0; color: #666; }
  .featured .service-text { color: #fff; }
  .more { font-style: italic; color: var(--brand-blue); font-size: 9px; }
  .featured .more { color: #a9c6f2; }

  .section-heading { font-family: var(--serif); font-size: 19px; color: var(--heading-blue); line-height: 23px; }
  .sub-heading { font-family: var(--serif); font-size: 14.5px; color: #333; }
  .body-text { font-size: 9px; line-height: 15.5px; color: #666; }

  .photo-about { left: 101px; top: 712px; width: 169px; height: 127px; background: linear-gradient(135deg, #c9d3dc, #8aa0b6 60%, #5d6b7a); }
  .photo-map { left: 595px; top: 733px; width: 232px; height: 144px; background: radial-gradient(circle at 30% 40%, #3f8fd8 0 20%, transparent 35%), radial-gradient(circle at 70% 40%, #c23a7a 0 18%, transparent 34%), radial-gradient(circle at 55% 60%, #f09a3a 0 12%, transparent 26%), #f3f3f3; }

  .test-arrow { top: 935px; width: 16px; height: 17px; background: #888; }
  .photo-client { left: 101px; top: 969px; width: 66px; height: 65px; background: linear-gradient(135deg, #e7d4c6, #b48f78); }
  .quote-box { left: 193px; top: 968px; width: 634px; height: 112px; background: #f0f0f0; padding: 18px 20px 0 20px; }
  .quote-box::before { content: ""; position: absolute; left: -12px; top: 22px; border: 12px solid transparent; border-left: 0; border-right-color: #f0f0f0; }
  .quote-text { font-size: 9.5px; line-height: 21px; font-style: italic; color: #777; }

  .footer { left: 0; top: 1118px; width: 928px; height: 82px; background: linear-gradient(180deg, var(--footer-top), var(--footer-bottom)); color: #fff; font-size: 10px; }
  .top-btn { left: 794px; top: 27px; width: 33px; height: 33px; background: #2f2f2f; color: #fff; font-size: 8px; text-align: center; padding-top: 8px; line-height: 10px; }
</style>
</head>
<body>

<div class="abs topbar"><span class="abs lang">English ⌄</span></div>

<header class="abs header">
  <div class="abs nav-active-bar"></div>
  <div class="abs brand"><span class="brand-mark"></span><span class="brand-name">TORVEL CAPITAL</span></div>
  <nav class="abs nav">
    <a class="active" style="left:409px">Home</a>
    <a style="left:460px">About</a>
    <a style="left:515px">Services ⌄</a>
    <a style="left:589px">Current Engagements</a>
    <a style="left:715px">Completed Transactions</a>
  </nav>
</header>

<section class="abs hero" role="img" aria-label="Photo of a smiling businesswoman with colleagues in a bright office"></section>
<div class="abs hero-caption" style="top:203px">Global, Professional, Trusted...</div>
<div class="abs hero-caption" style="top:255px">or Disciplined / Effective?</div>
<div class="abs hero-arrow" style="left:0"><svg width="36" height="37"><path d="M21 11l-7 7.5 7 7.5" stroke="#fff" stroke-width="2.5" fill="none"/></svg></div>
<div class="abs hero-arrow" style="left:891px"><svg width="37" height="37"><path d="M15 11l7 7.5-7 7.5" stroke="#fff" stroke-width="2.5" fill="none"/></svg></div>

<div class="abs service-card featured" style="left:101px">
  <div class="service-icon"><svg width="24" height="24" viewBox="0 0 24 24"><circle cx="12" cy="12" r="7" fill="none" stroke="#1f4a93" stroke-width="5" stroke-dasharray="3.5 2"/><circle cx="12" cy="12" r="5" fill="#1f4a93"/><circle cx="12" cy="12" r="2.5" fill="#fff"/></svg></div>
  <div class="service-title">Strategic Advisory<br>Services</div>
  <p class="service-text">Vero iudico intellegat no quo, priut nullam omittantur eam vivendo oportere. <span class="more">Learn More &gt;&gt;</span></p>
</div>
<div class="abs service-card" style="left:287px">
  <div class="service-icon"><svg width="22" height="22" viewBox="0 0 22 22"><path d="M3 3h16v10l-6 6H3z" fill="#444"/><path d="M9 8h6v6l-2-2-3 3-2-2 3-3z" fill="#fff"/></svg></div>
  <div class="service-title">Current Engagements</div>
  <p class="service-text">Vero iudico intellegat no quo, priut nullam omittantur eam vivendo oportere dolor in repre<br><span class="more">Learn More &gt;&gt;</span></p>
</div>
<div class="abs service-card" style="left:471px">
  <div class="service-icon"><svg width="26" height="22" viewBox="0 0 26 22"><rect x="1" y="2" width="24" height="18" rx="2" fill="#444"/><circle cx="15" cy="9" r="4" fill="#fff"/><rect x="4" y="15" width="18" height="2" fill="#fff"/></svg></div>
  <div class="service-title">Completed Transactions</div>
  <p class="service-text">Vero iudico intellegat no quo, priut nullam omittantur eam vivendo oportere dolor in repre<br><span class="more">Learn More &gt;&gt;</span></p>
</div>
<div class="abs service-card" style="left:657px">
  <div class="service-icon"><svg width="22" height="22" viewBox="0 0 22 22"><path d="M11 11a2 2 0 1 1 2-2a4 4 0 1 1-6 3a6 6 0 1 1 10 2a8 8 0 0 1-9 6" fill="none" stroke="#444" stroke-width="2"/></svg></div>
  <div class="service-title">Regulatory Compliance</div>
  <p class="service-text">Vero iudico intellegat no quo, priut nullam omittantur eam vivendo oportere dolor in repre<br><span class="more">Learn More &gt;&gt;</span></p>
</div>

<h2 class="abs section-heading" style="left:101px;top:679px">Who we are</h2>
<div class="abs photo-about" role="img" aria-label="Photo of a businessman sitting at a laptop in an office"></div>
<h3 class="abs sub-heading" style="left:287px;top:706px">Our Clients</h3>
<p class="abs body-text" style="left:287px;top:734px;width:290px">Torvel Capital has a diverse array of clients ranging from multi-billion dollar strategic acquirers to large private equity funds. We will not engage a client as a buyer if we believe there is any chance of them wasting our time or a prospective seller's time.</p>
<h3 class="abs sub-heading" style="left:287px;top:806px">Our Process</h3>
<p class="abs body-text" style="left:287px;top:830px">o&nbsp;&nbsp;&nbsp;&nbsp;&nbsp;Technology</p>
<p class="abs body-text" style="left:101px;top:856px;width:476px;line-height:16.5px">Once we have your acquisition parameters, we feed these into our software to create an initial target list. The criteria used to create this list can include geography, revenue targets, earning targets. <span class="more">Read More &gt;&gt;</span></p>

<h2 class="abs section-heading" style="left:596px;top:680px">Global Investment Banking<br>Services</h2>
<div class="abs photo-map" role="img" aria-label="Colourful world map illustration with location pins"></div>

<h2 class="abs section-heading" style="left:100px;top:927px">Testimonials</h2>
<div class="abs test-arrow" style="left:792px"><svg width="16" height="17"><path d="M9.5 5l-3.5 3.5 3.5 3.5" stroke="#fff" fill="none" stroke-width="1.5"/></svg></div>
<div class="abs test-arrow" style="left:810px"><svg width="16" height="17"><path d="M6.5 5l3.5 3.5-3.5 3.5" stroke="#fff" fill="none" stroke-width="1.5"/></svg></div>
<div class="abs photo-client" role="img" aria-label="Portrait photo of the client giving the testimonial"></div>
<div class="abs" style="left:101px;top:1043px;width:66px;text-align:center;font-size:10px;color:var(--brand-blue)">MARCUS</div>
<div class="abs" style="left:107px;top:1059px;font-size:11px;letter-spacing:1px"><span style="color:var(--brand-blue-dark)">★★★</span><span style="color:#bbb">★★</span></div>
<div class="abs quote-box">
  <p class="quote-text"><span style="font-family:var(--serif);font-size:22px;font-style:normal;color:#999;vertical-align:-4px">“</span>&nbsp; Sed ut perspiciatis unde omnis iste natus error sit voluptatem accusantium doloremque laudantium, totam rem aperiam, eaque ipsa quae ab illo inventore veritatis et quasi architecto beatae vitae dicta sunt explicabo. Nemo enim ipsam voluptatem quia voluptas sit aspernatur aut odit aut fugit. doloremque laudantium, totam rem aperiam, eaque ipsa quae ab illo inventore.</p>
</div>

<footer class="abs footer">
  <p class="abs" style="left:104px;top:22px">Desmond Harlow &nbsp;-&nbsp; 555.310.4826(m) &nbsp;-&nbsp; dharlow@torvelcapital.com</p>
  <p class="abs" style="left:104px;top:46px">Torvelsite.com ©2014 All Right Reserved.</p>
  <div class="abs top-btn">︿<br>TOP</div>
</footer>

</body>
</html>
```